Real Estate Webpage Design

We have an existing website: ferndaleestatecollective.com.au
We focus customised service mainly on Property Management and second-hand property sales.
We are not entirely happy about the current design and layout can stay roughly the same as the back end coding is linked to a CRM system.
We would like to see the design are more reachable to our clients and appearing.
Please check our Website Design Draft for more details.

Industry/Entity Type

Real estate Agency

Number of Pages Required

5+ page

Font styles to use
Sans Serif

Colors

Designer to choose colors to be used in the design.

```html
<!DOCTYPE html>
<html lang="en">
<head>
<meta charset="utf-8">
<title>Ferndale Estate Collective</title>
<link href="https://fonts.googleapis.com/css2?family=Poppins:wght@500;600;700&family=Roboto:wght@400;500;700&display=swap" rel="stylesheet">
<style>
:root{
  --gold:#f0bf4c;
  --gold-dark:#d9a73a;
  --navy:#2d3a4f;
  --navy-deep:#1f2735;
  --ink:#1c2230;
  --text:#5d6470;
  --grey-bg:#f2f2f3;
  --line:#e3e3e6;
  --white:#ffffff;
}
*{box-sizing:border-box;margin:0;padding:0}
html,body{width:1200px;height:3982px;overflow:hidden}
body{position:relative;font-family:"Roboto",sans-serif;color:var(--ink);background:var(--white)}
.abs{position:absolute}
h1,h2,h3{font-family:"Poppins",sans-serif}
.accent{color:var(--gold)}
.mark{display:inline-block;width:22px;height:22px;border:3px solid var(--gold);border-radius:4px;vertical-align:middle;margin-right:10px;position:relative;top:-3px}

/* top bar */
.topbar{top:0;left:0;width:1200px;height:37px;background:var(--navy);color:#fff;font-size:13px}
.topbar span{position:absolute;top:11px;display:flex;align-items:center;gap:8px}
.topbar svg{fill:#fff}
.topbar .phone{font-size:18px;font-weight:700;top:8px}

/* nav */
.nav{top:37px;left:0;width:1200px;height:71px;background:#fff;border-bottom:1px solid var(--line)}
.brand{position:absolute;left:111px;top:20px;display:flex;align-items:center;gap:8px;font-family:"Poppins",sans-serif;font-weight:600;font-size:22px;color:var(--navy)}
.brand i{width:24px;height:24px;background:var(--gold);border-radius:3px;display:block}
.menu{position:absolute;left:318px;top:28px;display:flex;gap:27px;font-size:13px;font-weight:700}
.menu a{color:var(--ink);text-decoration:none}
.menu a.active{color:var(--gold);font-weight:500}
.lang{position:absolute;left:892px;top:25px;display:flex;align-items:center;gap:10px;font-size:13px;font-weight:500}
.lang i{width:24px;height:24px;border-radius:50%;background:#d9dde6;display:block}
.login{position:absolute;left:996px;top:19px;width:92px;height:36px;background:var(--gold);color:#fff;font-size:12px;font-weight:700;display:flex;align-items:center;justify-content:center;border-radius:3px}

/* hero */
.hero{top:108px;left:0;width:1200px;height:598px}
.hero-photo{position:absolute;inset:0;background:linear-gradient(180deg,#1e7ed6 0%,#4aa2e8 38%,#8fb7cc 55%,#6c7b78 68%,#2f6b9a 78%,#1c5d93 100%);clip-path:polygon(0 0,100% 0,100% 82%,50% 97%,0 82%)}
.hero-band{position:absolute;inset:0;background:var(--gold);clip-path:polygon(0 81%,50% 96%,100% 81%,100% 84%,50% 100%,0 84%)}
.hero-copy{position:absolute;left:0;width:1200px;text-align:center;color:#fff}
.hero .welcome{top:62px;font-family:"Poppins",sans-serif;font-weight:600;font-size:31px}
.hero .title{top:96px;font-family:"Poppins",sans-serif;font-weight:700;font-size:54px;color:var(--gold)}
.hero .sub{top:178px;font-size:16px;font-weight:500;line-height:25px}
.arrow-btn{position:absolute;width:40px;height:40px;border-radius:50%;background:#fff;display:flex;align-items:center;justify-content:center;box-shadow:0 2px 6px rgba(0,0,0,.15)}
.hex-btn{position:absolute;height:46px;display:flex;align-items:center;justify-content:center;font-size:13px;font-weight:700;color:var(--navy);background:var(--navy);clip-path:polygon(14px 0,calc(100% - 14px) 0,100% 50%,calc(100% - 14px) 100%,14px 100%,0 50%)}
.hex-btn .fill{position:absolute;inset:0 6px;background:var(--gold);clip-path:polygon(12px 0,calc(100% - 12px) 0,100% 50%,calc(100% - 12px) 100%,12px 100%,0 50%)}
.hex-btn .label{position:relative;display:flex;align-items:center;gap:10px}
.hex-btn.dark{background:var(--gold)}
.hex-btn.dark .fill{background:var(--navy)}
.hex-btn.dark .label{color:#fff}
.dot{width:13px;height:13px;border-radius:50%;background:var(--navy);display:inline-flex;align-items:center;justify-content:center}
.dot::after{content:"";border-left:5px solid var(--gold);border-top:3px solid transparent;border-bottom:3px solid transparent;margin-left:2px}

/* about */
.about-img{top:757px;left:153px;width:345px;height:375px;background:linear-gradient(135deg,#a9bccd,#7f909f 55%,#c3ccd3)}
.about-text{top:770px;left:600px;width:486px}
.about-text h2{font-size:29px;font-weight:700;color:var(--navy);margin-bottom:24px}
.about-text p{font-size:14.5px;line-height:26.5px;color:var(--text);text-align:justify;margin-bottom:25px}

/* listings */
.listings-bg{top:1186px;left:0;width:1200px;height:640px;background:var(--grey-bg);clip-path:polygon(0 17%,50% 0,100% 17%,100% 100%,0 100%)}
.listings-edge{top:1186px;left:0;width:1200px;height:120px;background:var(--gold);clip-path:polygon(0 94%,50% 0,100% 94%,100% 97%,50% 6%,0 97%)}
.section-title{left:0;width:1200px;text-align:center;font-size:29px;font-weight:700;color:var(--navy)}
.tabs{top:1368px;left:0;width:1200px;display:flex;justify-content:center;gap:38px;font-size:14.5px;font-weight:500}
.tabs span{padding-bottom:10px}
.tabs .on{color:var(--gold);border-bottom:3px solid var(--gold)}
.card{width:320px;height:330px;top:1440px}
.card .photo{position:absolute;left:0;top:0;width:300px;height:222px;background:linear-gradient(160deg,#a8c3dc,#7f93a6 55%,#c7b79c)}
.card .tag{position:absolute;left:10px;top:15px;background:var(--gold);font-size:11px;font-weight:700;padding:4px 8px;color:var(--navy)}
.card .info{position:absolute;left:60px;top:163px;width:262px;height:168px;background:#fff;box-shadow:0 4px 14px rgba(0,0,0,.1);padding:18px 18px}
.info h3{font-family:"Roboto",sans-serif;font-size:14px;font-weight:500;margin-bottom:14px}
.feats{display:flex;gap:24px;font-size:13px;font-weight:700;margin-bottom:14px}
.feats i{display:inline-block;width:16px;height:9px;background:var(--gold);border-radius:2px;margin-right:12px}
.price{display:flex;align-items:center;gap:16px;color:var(--gold);font-size:18px;font-weight:500;margin-bottom:10px}
.price em{width:12px;height:12px;border-radius:50%;border:2px solid var(--ink);display:inline-block}
.info .lbl{font-size:13px;font-weight:700;margin-bottom:8px}
.info .date{font-size:13px;color:var(--text)}

/* team */
.skyline{top:1760px;left:110px;width:980px;height:110px;background:linear-gradient(180deg,#c9cbcf,#9b9ea4)}
.team-bg{top:1822px;left:0;width:1200px;height:684px;background:var(--navy);clip-path:polygon(0 0,50% 14%,100% 0,100% 100%,0 100%)}
.team-edge{top:1822px;left:0;width:1200px;height:140px;background:var(--gold);clip-path:polygon(0 0,50% 52%,100% 0,100% 4%,50% 60%,0 4%)}
.member{width:250px;top:2065px;text-align:center;color:#fff}
.member .pic{width:224px;height:224px;margin:0 auto;border-radius:50%;border:5px solid var(--gold);background:linear-gradient(180deg,#d5d6d8,#9fa3a9 60%,#2a2c33)}
.member h3{font-family:"Roboto",sans-serif;font-size:22px;font-weight:700;margin-top:15px}
.member p{font-size:13.5px;margin-top:6px}

/* testimonials */
.clients{top:2580px;left:111px;width:368px}
.clients h2{font-size:29px;font-weight:700;color:var(--navy);margin-bottom:18px}
.clients p{font-size:14.5px;line-height:24px;color:var(--text);text-align:justify}
.circle-arrow{position:absolute;width:40px;height:40px;border-radius:50%;display:flex;align-items:center;justify-content:center}
.quote{width:228px;height:255px;top:2597px}
.quote .head{position:absolute;left:0;top:0;width:100%;height:78px;background:var(--gold);border-radius:40px 0 0 0}
.quote .face{position:absolute;left:0;top:0;width:78px;height:78px;border-radius:50%;border:3px solid var(--gold);background:linear-gradient(180deg,#dfe0e2,#8c929a)}
.quote .who{position:absolute;left:100px;top:18px;font-size:15px;line-height:19px;color:var(--navy)}
.quote .who b{font-weight:500;display:block}
.quote .body{position:absolute;left:22px;top:78px;width:206px;height:177px;background:#fff;box-shadow:0 3px 12px rgba(0,0,0,.1);padding:14px 14px;font-size:12px;line-height:20px;color:var(--text);text-align:justify}
.quote .qm{font-family:"Poppins",sans-serif;font-size:40px;color:var(--gold);line-height:30px;height:30px;font-weight:700}

/* contact */
.contact{top:2945px;left:0;width:1200px;height:640px;background:linear-gradient(180deg,#f1c253,#ebb63f)}
.contact h2{position:absolute;top:56px;left:0;width:1200px;text-align:center;font-size:29px;font-weight:700;color:#fff}
.field-lbl{font-size:14px;font-weight:700;color:#fff}
.field{background:#fff;border:1px solid #e8d7b0;border-radius:3px;width:383px;height:50px;padding:16px 13px;font-size:13.5px;color:#555}
.submit{top:3391px;left:518px;width:164px;height:48px;border-radius:24px;background:var(--navy);color:#fff;font-size:13px;font-weight:700;display:flex;align-items:center;justify-content:center;gap:10px}

/* footer */
.footer{top:3470px;left:0;width:1200px;height:512px;background:var(--navy-deep);clip-path:polygon(0 20%,50% 0,100% 20%,100% 100%,0 100%)}
.f-col h3{font-family:"Roboto",sans-serif;font-size:20px;font-weight:700;color:#fff;padding-bottom:10px;border-bottom:3px solid var(--gold);display:inline-block;line-height:26px}
.f-col{color:#fff}
.pin{width:26px;height:26px;border-radius:50%;background:var(--gold);display:flex;align-items:center;justify-content:center;position:absolute}
.sub-box{top:3744px;left:504px;width:298px;height:46px;border-radius:23px;background:#fff;border:2px solid var(--gold)}
.sub-box span{position:absolute;left:18px;top:14px;font-size:12px;color:#777}
.sub-box b{position:absolute;right:3px;top:3px;width:110px;height:36px;border-radius:18px;background:var(--gold);font-size:12px;font-weight:700;color:var(--navy);display:flex;align-items:center;justify-content:center}
.social{top:3690px;left:886px;display:flex;gap:9px}
.social i{width:31px;height:31px;border-radius:50%;border:2px solid #fff;background:var(--gold);display:block}
.foot-nav{top:3872px;left:0;width:1200px;display:flex;justify-content:center;gap:18px;color:#fff;font-size:14px;font-weight:700}
.foot-nav em{font-style:normal;font-weight:400}
.copy{top:3928px;left:0;width:1200px;text-align:center;color:#fff;font-size:14px}
</style>
</head>
<body>

<!-- top bar -->
<div class="abs topbar">
  <span style="left:111px"><svg width="13" height="11" viewBox="0 0 13 11"><path d="M0 0h13v11H0zM1 1.5v.6l5.5 3.6L12 2.1v-.6z" fill-rule="evenodd"/></svg>info@ferndaleestate.com.au</span>
  <span style="left:471px"><svg width="12" height="12" viewBox="0 0 12 12"><circle cx="6" cy="6" r="5" fill="none" stroke="#fff" stroke-width="1.6"/><path d="M6 3v3.3l2 1.2" stroke="#fff" stroke-width="1.4" fill="none"/></svg>Monday – Friday : 8:30 am – 5:00pm</span>
  <span class="phone" style="left:940px"><svg width="14" height="14" viewBox="0 0 24 24"><path d="M6.6 10.8a15 15 0 006.6 6.6l2.2-2.2a1 1 0 011-.25 11 11 0 003.6.57 1 1 0 011 1V20a1 1 0 01-1 1A17 17 0 013 4a1 1 0 011-1h3.5a1 1 0 011 1c0 1.25.2 2.45.57 3.57a1 1 0 01-.25 1z"/></svg>02 6000 4127</span>
</div>

<!-- nav -->
<header class="abs nav">
  <div class="brand"><i></i>Ferndale</div>
  <nav class="menu">
    <a class="active">Home</a><a>About Us</a><a>Leasing</a><a>Buy</a><a>Sell</a><a>Our Team</a><a>Blog</a><a>Contact Us</a>
  </nav>
  <div class="lang"><i></i>Eng <svg width="8" height="5"><path d="M0 0h8L4 5z" fill="#1c2230"/></svg></div>
  <div class="login">LOG IN &nbsp;<svg width="9" height="10" viewBox="0 0 9 10"><rect y="4" width="9" height="6" fill="#fff"/><path d="M2 4V3a2.5 2.5 0 015 0v1" stroke="#fff" stroke-width="1.4" fill="none"/></svg></div>
</header>

<!-- hero -->
<section class="abs hero">
  <div class="hero-photo" role="img" aria-label="City skyline of high-rise apartments across a lake under a blue sky"></div>
  <div class="hero-band"></div>
  <div class="hero-copy welcome">Welcome to</div>
  <h1 class="hero-copy title">Ferndale Estate Collective</h1>
  <p class="hero-copy sub">Ferndale means “a valley of ferns, a place to settle”, buying a property is one of the most<br>expensive expenses &amp; important assets for people</p>
  <div class="hex-btn" style="left:508px;top:242px;width:184px"><i class="fill"></i><span class="label">GET STARTED <i class="dot"></i></span></div>
  <div class="arrow-btn" style="left:36px;top:260px"><svg width="10" height="14"><path d="M8 1L2 7l6 6" stroke="#1c2230" stroke-width="2" fill="none"/></svg></div>
  <div class="arrow-btn" style="left:1124px;top:260px"><svg width="10" height="14"><path d="M2 1l6 6-6 6" stroke="#1c2230" stroke-width="2" fill="none"/></svg></div>
</section>

<!-- about -->
<div class="abs about-img" role="img" aria-label="Collage of residential apartment buildings and streetscapes"></div>
<section class="abs about-text">
  <h2><span class="mark"></span>Who <span class="accent">We Are</span></h2>
  <p>Ferndale means “a valley of ferns, a place to settle”, buying a property is one of the most expensive expenses and important assets for people. Ferndale is a real estate company located in Marlow, the capital region.</p>
  <p>Being a portfolio sales agent and property manager, coupled with our high–profile international real estate experience, Ferndale is considered a market leader on the cutting edge with deep industry knowledge, ranging from landlord–tenant relationships, residential purchases.</p>
  <div class="hex-btn" style="position:relative;width:184px"><i class="fill"></i><span class="label">LEARN MORE <i class="dot"></i></span></div>
</section>

<!-- listings -->
<div class="abs listings-bg"></div>
<div class="abs listings-edge"></div>
<h2 class="abs section-title" style="top:1298px"><span class="mark"></span>This Month At <span class="accent">Ferndale Estate Collective</span></h2>
<div class="abs tabs"><span class="on">FOR SALE</span><span>FOR LEASE</span><span>OPEN TIMES</span><span>SOLD</span><span>LEASED</span></div>

<div class="arrow-btn" style="left:36px;top:1552px"><svg width="10" height="14"><path d="M8 1L2 7l6 6" stroke="#1c2230" stroke-width="2" fill="none"/></svg></div>
<div class="arrow-btn" style="left:1124px;top:1552px"><svg width="10" height="14"><path d="M2 1l6 6-6 6" stroke="#1c2230" stroke-width="2" fill="none"/></svg></div>

<article class="abs card" style="left:94px">
  <div class="photo" role="img" aria-label="Apartment tower with a rooftop pool overlooking the lake"></div>
  <span class="tag">MARLOW</span>
  <div class="info">
    <h3>Level 5/22/3 Harbour View Av</h3>
    <div class="feats"><span><i></i>2</span><span><i></i>1</span><span><i></i>1</span></div>
    <div class="price">$500,000+ <em></em><em></em><em></em></div>
    <div class="lbl">Next Inspection :</div>
    <div class="date">Sat 21st May 09:40 AM - 10:00 AM</div>
  </div>
</article>
<article class="abs card" style="left:438px">
  <div class="photo" role="img" aria-label="Modern apartment block with balconies and trees"></div>
  <span class="tag">MARLOW</span>
  <div class="info">
    <h3>Level 5/22/3 Harbour View Av</h3>
    <div class="feats"><span><i></i>2</span><span><i></i>1</span><span><i></i>1</span></div>
    <div class="price">$500,000+ <em></em><em></em><em></em></div>
    <div class="lbl">Next Inspection :</div>
    <div class="date">Sat 21st May 09:40 AM - 10:00 AM</div>
  </div>
</article>
<article class="abs card" style="left:782px">
  <div class="photo" role="img" aria-label="Contemporary two-storey house with glass frontage"></div>
  <span class="tag">MARLOW</span>
  <div class="info">
    <h3>Level 5/22/3 Harbour View Av</h3>
    <div class="feats"><span><i></i>2</span><span><i></i>1</span><span><i></i>1</span></div>
    <div class="price">$500,000+ <em></em><em></em><em></em></div>
    <div class="lbl">Next Inspection :</div>
    <div class="date">Sat 21st May 09:40 AM - 10:00 AM</div>
  </div>
</article>

<!-- team -->
<div class="abs skyline" role="img" aria-label="Grey silhouette of city landmarks"></div>
<div class="abs team-bg"></div>
<div class="abs team-edge"></div>
<h2 class="abs section-title" style="top:1993px;color:#fff"><span class="mark"></span>Our <span class="accent">Team</span></h2>
<div class="abs member" style="left:98px"><div class="pic" role="img" aria-label="Portrait of the principal"></div><h3>Leo Hartley</h3><p>Principal</p></div>
<div class="abs member" style="left:350px"><div class="pic" role="img" aria-label="Portrait of the business relationship manager"></div><h3>Nina Castell</h3><p>Business Relationship Manager</p></div>
<div class="abs member" style="left:600px"><div class="pic" role="img" aria-label="Portrait of the property manager"></div><h3>Clara Voss</h3><p>Property Manager</p></div>
<div class="abs member" style="left:851px"><div class="pic" role="img" aria-label="Portrait of the property manager assistant"></div><h3>Iris Penrose</h3><p>Property Manager Assistant</p></div>
<div class="hex-btn dark" style="left:508px;top:2392px;width:184px"><i class="fill"></i><span class="label">VIEW ALL <i class="dot" style="background:var(--gold)"></i></span></div>

<!-- testimonials -->
<section class="abs clients">
  <h2><span class="mark"></span>What Our <span class="accent">Clients Say</span></h2>
  <p>Lorem ipsum dolor sit amet, consectetur adipiscing elit, sed do eiusmod tempor incididunt ut labore et dolore magna aliqua. Ut enim ad minim veniam, quis nostrud exercitation ullamco laboris nisi ut aliquip ex ea commodo consequat. Duis aute irure dolor in reprehenderit in voluptate velit esse cillum dolore eu fugiat nulla pariatur.</p>
</section>
<div class="circle-arrow" style="left:111px;top:2828px;border:1px solid var(--line)"><svg width="18" height="10"><path d="M17 5H2M6 1L2 5l4 4" stroke="#1c2230" stroke-width="2" fill="none"/></svg></div>
<div class="circle-arrow" style="left:163px;top:2828px;background:var(--gold);border:3px solid #f7dc9b"><svg width="18" height="10"><path d="M1 5h15M12 1l4 4-4 4" stroke="#1c2230" stroke-width="2" fill="none"/></svg></div>

<article class="abs quote" style="left:526px"><div class="head"></div><div class="face" role="img" aria-label="Client portrait"></div><div class="who"><b>John Doe</b>Businessman</div><div class="body"><div class="qm">“</div>I would highly recommend Ferndale property to you, they were helping me manage my investment property, they found a quality tenant in 2 days and maintain</div></article>
<article class="abs quote" style="left:758px"><div class="head"></div><div class="face" role="img" aria-label="Client portrait"></div><div class="who"><b>John Doe</b>Businessman</div><div class="body"><div class="qm">“</div>I would highly recommend Ferndale property to you, they were helping me manage my investment property, they found a quality tenant in 2 days and maintain</div></article>
<article class="abs quote" style="left:989px"><div class="head"></div><div class="face" role="img" aria-label="Client portrait"></div><div class="who"><b>John Doe</b>Businessman</div><div class="body"><div class="qm">“</div>I would highly recommend Ferndale property to you, they were helping me manage my investment property, they found a quality tenant in 2 days and maintain</div></article>

<!-- contact -->
<section class="abs contact">
  <h2><span class="mark" style="border-color:var(--navy)"></span>Get In Touch</h2>
  <div class="abs field-lbl" style="left:223px;top:135px">Your Name</div>
  <div class="abs field" style="left:210px;top:156px">John Smith</div>
  <div class="abs field-lbl" style="left:620px;top:135px">Company</div>
  <div class="abs field" style="left:607px;top:156px">ABC Company</div>
  <div class="abs field-lbl" style="left:223px;top:235px">Email Address</div>
  <div class="abs field" style="left:210px;top:256px">johnsmith@gmail.com</div>
  <div class="abs field-lbl" style="left:620px;top:235px">Message</div>
  <div class="abs field" style="left:607px;top:256px;height:150px">What do you talk about ....</div>
  <div class="abs field-lbl" style="left:223px;top:335px">Phone</div>
  <div class="abs field" style="left:210px;top:356px">1 888 888 888</div>
</section>
<div class="abs submit">SUBMIT NOW <i class="dot" style="background:#fff"></i></div>

<!-- footer -->
<footer class="abs footer"></footer>
<div class="abs f-col" style="left:111px;top:3625px"><h3>Address</h3></div>
<div class="pin" style="left:111px;top:3700px"><svg width="10" height="13" viewBox="0 0 10 13"><path d="M5 0a5 5 0 015 5c0 3.5-5 8-5 8S0 8.5 0 5a5 5 0 015-5z" fill="#fff"/><circle cx="5" cy="5" r="1.8" fill="#f0bf4c"/></svg></div>
<div class="abs" style="left:157px;top:3696px;color:#fff;font-size:14px;font-weight:500;line-height:23px">18/4 Willow Crest Rd, Marlow,<br>ACT, 2900</div>
<div class="pin" style="left:111px;top:3753px"><svg width="12" height="12" viewBox="0 0 24 24"><path fill="#fff" d="M6.6 10.8a15 15 0 006.6 6.6l2.2-2.2a1 1 0 011-.25 11 11 0 003.6.57 1 1 0 011 1V20a1 1 0 01-1 1A17 17 0 013 4a1 1 0 011-1h3.5a1 1 0 011 1c0 1.25.2 2.45.57 3.57a1 1 0 01-.25 1z"/></svg></div>
<div class="abs" style="left:157px;top:3754px;color:#fff;font-size:19px;font-weight:700">02 6000 4127</div>

<div class="abs f-col" style="left:503px;top:3625px"><h3>Subscribe Newsletter</h3></div>
<div class="abs" style="left:503px;top:3680px;width:290px;color:#fff;font-size:14px;line-height:19px">Lorem ipsum dolor sit amet, consectetur adipiscing elit, sed do eiusmod</div>
<div class="abs sub-box"><span>✉ Email Address *</span><b>SUBSCRIBE</b></div>

<div class="abs f-col" style="left:886px;top:3625px"><h3>Follow Us On</h3></div>
<div class="abs social"><i></i><i></i><i></i><i></i><i></i></div>

<nav class="abs foot-nav"><span>HOME</span><em>/</em><span>ABOUT</span><em>/</em><span>LEASING</span><em>/</em><span>BUY</span><em>/</em><span>SELL</span><em>/</em><span>OUR TEAM</span><em>/</em><span>BLOG</span><em>/</em><span>CONTACT</span></nav>
<div class="abs copy">© 2022 Ferndale. All Rights Reserved</div>

</body>
</html>
```